Farm business needs label design for product

We need a label design for our tomato product. Product is yellow tomato and need good design to attract customers.
Updates
Low design quality
Target Market(s)
house wife
Industry/Entity Type
Agriculture
Colors
Requirements
Must have
- Label must contains
- - Product Name : "Little crisp moon Tomatoes"
- - 200g Net
- - "Grown in Australia Logo"
- - Kelvora Logo
- - "Grown & Packed bu :
- B'Rundel Logo
- 518, Dunmore Road,
- Orvale Flats, SA 5987
- Australia
- www.brundel.com.au
- -Facebook Logo : Kelvora
- -Barcode
- - "Always Fresh All The Time"
- -Label Size : 75mm X 40mm
- - Label must be Transparent (See Through)
- all logos I have added and also add one model girl if you can add on label
Nice to have
- Our Slogan is "Always Fresh All The Time" so design looks fresh and nice feeling

```html
<!DOCTYPE html>
<html lang="en">
<head>
<meta charset="utf-8">
<title>Kelvora – Little Crisp Moon Tomatoes Label</title>
<link href="https://fonts.googleapis.com/css2?family=Oswald:wght@400;500&family=Open+Sans:wght@400;600&display=swap" rel="stylesheet">
<style>
  :root {
    --bg: #1c1c1c;
    --label-green: #0c4f38;
    --label-black: #000000;
    --accent-yellow: #f2e600;
    --accent-green: #2aa14a;
    --brand-green: #7cc242;
    --text-light: #ffffff;
  }
  * { margin: 0; padding: 0; box-sizing: border-box; }
  html, body { width: 1168px; height: 1200px; overflow: hidden; background: var(--bg); }
  .canvas { position: relative; width: 1168px; height: 1200px; }
  .label {
    position: absolute; left: 34px; top: 305px;
    width: 1100px; height: 590px;
    border-radius: 16px; overflow: hidden;
    background: var(--label-black);
    font-family: "Open Sans", sans-serif; color: var(--text-light);
  }
  .label-shapes { position: absolute; inset: 0; }
  .fresh-badge {
    position: absolute; left: 419px; top: 104px; width: 178px; height: 178px;
    border: 6px solid var(--accent-green); border-radius: 50%;
    display: flex; flex-direction: column; align-items: center; justify-content: center;
    font-family: "Oswald", sans-serif; line-height: 1;
  }
  .fresh-badge .small { font-size: 26px; font-weight: 400; }
  .fresh-badge .big { font-size: 52px; font-weight: 500; margin: 2px 0; }
  .fresh-badge .tiny { font-size: 21px; font-weight: 400; }
  .brand-mark {
    position: absolute; left: 700px; top: 128px;
    display: flex; align-items: center; gap: 8px;
    font-size: 24px; font-weight: 600; color: var(--brand-green);
  }
  .brand-mark .dot { width: 16px; height: 16px; border-radius: 50%; background: var(--brand-green); }
  .social {
    position: absolute; right: 44px; top: 42px;
    display: flex; align-items: center; gap: 6px;
    font-size: 26px; color: var(--brand-green);
  }
  .social .square { width: 24px; height: 24px; background: var(--brand-green); border-radius: 3px; }
  .product-name {
    position: absolute; right: 44px; top: 112px; text-align: right;
    font-family: "Oswald", sans-serif; font-weight: 500; font-size: 68px; line-height: 72px;
    text-transform: uppercase; letter-spacing: -0.5px;
  }
  .net-weight {
    position: absolute; left: 785px; top: 360px;
    font-family: "Oswald", sans-serif; font-size: 38px; font-weight: 400;
  }
  .packer-title {
    position: absolute; left: 560px; top: 452px;
    font-size: 19px; line-height: 21px;
  }
  .packer-brand {
    position: absolute; left: 483px; top: 506px;
    font-size: 34px; font-weight: 600; color: var(--text-light);
  }
  .packer-divider {
    position: absolute; left: 669px; top: 476px; width: 2px; height: 98px; background: var(--text-light);
  }
  .packer-address {
    position: absolute; left: 683px; top: 472px;
    font-size: 22px; line-height: 25px; font-style: normal;
  }
</style>
</head>
<body>
<div class="canvas">
  <div class="label">
    <svg class="label-shapes" width="1100" height="590" viewBox="0 0 1100 590">
      <defs>
        <linearGradient id="photoTone" x1="0" y1="0" x2="0" y2="1">
          <stop offset="0" stop-color="#f2f5f8"/>
          <stop offset="0.7" stop-color="#dfe4ea"/>
          <stop offset="1" stop-color="#f0c060"/>
        </linearGradient>
      </defs>
      <path role="img" aria-label="Photo of a smiling girl holding two small yellow tomatoes, more tomatoes on the table"
            d="M0 0 H290 C380 80 420 300 330 430 C290 500 250 560 210 590 H0 Z" fill="url(#photoTone)"/>
      <path d="M628 0 H665 C670 260 600 470 240 590 H205 C560 470 630 250 628 0 Z" fill="var(--accent-yellow)"/>
      <path d="M665 0 H1100 V590 H240 C600 470 670 260 665 0 Z" fill="var(--label-green)"/>
    </svg>

    <div class="fresh-badge">
      <span class="small">ALWAYS</span>
      <span class="big">FRESH</span>
      <span class="tiny">ALL THE TIME</span>
    </div>

    <div class="brand-mark"><span class="dot"></span>Kelvora</div>
    <div class="social"><span class="square"></span>/Kelvora</div>

    <h1 class="product-name">Little<br>Crisp Moon<br>Tomatoes</h1>

    <div class="net-weight">200g Net</div>

    <div class="packer-title">Grown &amp;<br>Packed By :</div>
    <div class="packer-brand">B'Rundel</div>
    <div class="packer-divider"></div>
    <address class="packer-address">
      518, Dunmore Road,<br>
      Orvale Flats, SA 5987<br>
      Australia<br>
      www.brundel.com.au
    </address>
  </div>
</div>
</body>
</html>
```